Front and back cover design for skincare marketing materials

Thank you for showing an interest in my project.
Project Details.

I require a front and back cover for our marketing materials.
·       Front Cover size: 105 mm W x 150 mm H.
·       Back Cover size:  105 mm W x 150 mm H.
·       It must include these two colors. You can use a third color if you wish.
1.     #DBA09D
2.     #FFFFFF
 
Front Cover
·      The front cover will have a faded image of the Kakadu Plum branch and fruit. There are two image files, KP_image-1.jpg and kp_image-2.jpeg. You can use both images, just a portion of them, or source alternative royalty-free images of Kakadu Plum that may better fit the design. These two files have been uploaded.
 
The front cover wording.
Top of the front cover.
a.     The title of the image. “Kakadu Plum”
b.     The brand name, “Vellora Skincare”. The file brand_name.ai uploaded.
 
Bottom of the front cover- Designer's choice of font.
The bottom of the front cover contains three lines of text in the following order.  
1.     Australian Native Ingredients
2.     100% Natural · Organic · Wild-harvested
3.     Australian-Made Premium Skincare
 
Back Cover
·      Back Cover wording.The back cover contains the following words "grown by nature" in white (#FFFFFF) of font Italianno (font_file.ttf) with a background color of #DBA09D as seen in the sample box (sample_box.pdf) right-side panel
 
Please provide one file for the front cover and a separate file for the back cover.
All the elements of the files must be editable.
 
Do NOT use the Curve function on the files, as the text must remain editable/changeable.
 
All assets/resources/files, including fonts not supplied by us but used by the designer, must be named and provided with the finished design.
Updates

Slow to provide project details.

Target Market(s)

Beauty-minded Asian consumers between the ages of 32 and 75 who take a proactive approach to maintaining younger-looking skin. Those who already know the danger of skin damage caused by skincare containing harsh chemicals choose effective natural/organic solutions to meet their skincare needs. Those who wish a more radiant glow and youthful appearance to their skin. Usually, a two-income middle to high-income bracket couples with a mindset for health and beauty.

Industry/Entity Type

beauty

Font styles to use
Other font styles liked:
• I will provide a font file and a brand name file.

Requirements
Must have
• You must use the two colors provided on the product box. The designer may use a third color.
Nice to have
• some gold colour

```html
<!DOCTYPE html>
<html lang="en">
<head>
<meta charset="utf-8">
<title>Vellora Skincare – Kakadu Plum Cover Set</title>
<link href="https://fonts.googleapis.com/css2?family=Italianno&family=Poppins:wght@400;500&display=swap" rel="stylesheet">
<style>
  :root {
    --stage: #3a2627;
    --rose: #dba09d;
    --rose-soft: #e3aaa6;
    --blush: #f8e9e4;
    --peach: #f2caa8;
    --apricot: #ebbf8f;
    --ink: #1e1a1a;
    --white: #ffffff;
  }
  * { box-sizing: border-box; margin: 0; padding: 0; }
  html, body { width: 776px; height: 1200px; overflow: hidden; }
  body {
    background: var(--stage);
    font-family: "Poppins", sans-serif;
    position: relative;
  }
  .cover {
    position: absolute;
    top: 300px;
    width: 360px;
    height: 514px;
    overflow: hidden;
  }
  .cover--front { left: 18px; }
  .cover--back { left: 398px; background: var(--rose); }

  .front-photo {
    position: absolute; inset: 0;
    background:
      radial-gradient(ellipse 45% 35% at 52% 48%, rgba(242,196,160,0.85), transparent 70%),
      radial-gradient(ellipse 40% 30% at 88% 45%, rgba(235,191,143,0.7), transparent 70%),
      radial-gradient(ellipse 30% 25% at 8% 62%, rgba(240,180,185,0.6), transparent 70%),
      linear-gradient(180deg, var(--blush) 0%, #f4dcd2 25%, var(--peach) 55%, #e4b3a4 78%, var(--rose) 100%);
  }
  .brand {
    position: absolute; top: 88px; left: 0; right: 0;
    text-align: center;
    font-family: "Poppins", sans-serif;
    font-weight: 500;
    font-size: 15px;
    letter-spacing: 0.32em;
    padding-left: 0.32em;
    color: var(--rose);
  }
  .product-title {
    position: absolute; top: 186px; left: 0; right: 0;
    text-align: center;
    font-family: "Italianno", cursive;
    font-weight: 400;
    line-height: 0.7;
  }
  .product-title__first { display: block; font-size: 96px; color: var(--rose-soft); }
  .product-title__second { display: block; font-size: 96px; color: var(--ink); padding-left: 4px; }

  .claims {
    position: absolute; bottom: 44px; left: 0; right: 0;
    display: flex; justify-content: center; gap: 24px;
  }
  .claim-seal { width: 66px; height: 66px; }
  .claim-seal__ring { fill: none; stroke: var(--white); stroke-width: 0.8; }
  .claim-seal__text {
    fill: var(--white);
    font-family: "Poppins", sans-serif;
    font-weight: 500;
    font-size: 4.6px;
    letter-spacing: 0.35px;
  }

  .tagline {
    position: absolute;
    left: 50%; top: 50%;
    transform: translate(-50%, -50%) rotate(-90deg);
    white-space: nowrap;
    font-family: "Italianno", cursive;
    font-size: 84px;
    color: var(--white);
    line-height: 1;
  }

  .side-label {
    position: absolute; top: 858px;
    width: 360px; text-align: center;
    font-size: 26px; font-weight: 400;
    color: var(--white);
  }
  .side-label--front { left: 18px; }
  .side-label--back { left: 398px; }
</style>
</head>
<body>
  <svg width="0" height="0" style="position:absolute" aria-hidden="true">
    <defs>
      <path id="seal-arc-top" d="M 8,38 A 25.5,25.5 0 1 1 58,38"/>
      <path id="seal-arc-bottom" d="M 12,36 A 21.5,21.5 0 0 0 54,36"/>
    </defs>
  </svg>

  <section class="cover cover--front">
    <div class="front-photo" role="img" aria-label="Faded soft-focus photograph of a Kakadu Plum branch and fruit"></div>
    <div class="brand">VELLORA SKINCARE</div>
    <h1 class="product-title">
      <span class="product-title__first">Kakadu</span>
      <span class="product-title__second">Plum</span>
    </h1>
    <div class="claims">
      <svg class="claim-seal" viewBox="0 0 66 66">
        <circle class="claim-seal__ring" cx="33" cy="33" r="32"/>
        <text class="claim-seal__text" text-anchor="middle"><textPath href="#seal-arc-top" startOffset="50%">AUSTRALIAN NATIVE</textPath></text>
        <text class="claim-seal__text" text-anchor="middle"><textPath href="#seal-arc-bottom" startOffset="50%">INGREDIENTS</textPath></text>
      </svg>
      <svg class="claim-seal" viewBox="0 0 66 66">
        <circle class="claim-seal__ring" cx="33" cy="33" r="32"/>
        <text class="claim-seal__text" text-anchor="middle"><textPath href="#seal-arc-top" startOffset="50%">100% NATURAL · ORGANIC ·</textPath></text>
        <text class="claim-seal__text" text-anchor="middle"><textPath href="#seal-arc-bottom" startOffset="50%">WILD-HARVESTED</textPath></text>
      </svg>
      <svg class="claim-seal" viewBox="0 0 66 66">
        <circle class="claim-seal__ring" cx="33" cy="33" r="32"/>
        <text class="claim-seal__text" text-anchor="middle"><textPath href="#seal-arc-top" startOffset="50%">AUSTRALIAN-MADE PREMIUM</textPath></text>
        <text class="claim-seal__text" text-anchor="middle"><textPath href="#seal-arc-bottom" startOffset="50%">SKINCARE</textPath></text>
      </svg>
    </div>
  </section>

  <section class="cover cover--back">
    <p class="tagline">grown by nature</p>
  </section>

  <p class="side-label side-label--front">FRONT</p>
  <p class="side-label side-label--back">BACK</p>
</body>
</html>
```